Banner for promote service of debit card

We are PagoLume and we need the banners to be posted on the facebook and instagram pages.
We want something to communicate that it is an exclusive debit card full of services.
Low commissions.
Our competitors:
https://www.kelmora.example/it/home.html
https://www.zofe.example/it/
https://www.socialpage.example/ostrevabank/
monadrift
maybe some banner that makes the idea of a convenient debit card that everyone can use.
Girls enjoying card shopping.
Please check also website for slogans and phrases to use
https://www.pagolume.example/
Should show the services.
We must convey that it is a fast, simple card that guarantees privacy.
We need strong banners that attract people as these ban will be sponsored on instagram and facebook
People 18-35 y
Open Bank account. low commissions. Easy to use. No limits. 100% Privacy.
- Written in Italian.

```html
<!DOCTYPE html>
<html lang="it">
<head>
<meta charset="utf-8">
<title>PagoLume – Una carta per tutti</title>
<link rel="stylesheet" href="https://fonts.googleapis.com/css2?family=Open+Sans:wght@400;600;700&family=Montserrat:wght@800&display=swap">
<style>
  :root {
    --purple-deep: #2f0a7a;
    --purple-mid: #46108f;
    --purple-violet: #7a3bff;
    --purple-soft: #8a3aa8;
    --pink-hot: #ff3d9a;
    --pink-band: #f2457f;
    --pink-light: #f9a3c0;
    --yellow: #ffe22e;
    --white: #ffffff;
    --grey-logo: #b9b3cc;
    --line: rgba(160, 90, 255, 0.55);
  }
  * { margin: 0; padding: 0; box-sizing: border-box; }
  html, body { width: 1200px; height: 1200px; overflow: hidden; }
  body { background: var(--purple-deep); font-family: "Open Sans", Arial, sans-serif; }

  .banner {
    position: relative;
    width: 1200px;
    height: 1200px;
    overflow: hidden;
    background: linear-gradient(160deg, var(--purple-deep) 0%, var(--purple-mid) 55%, #5a1a9e 100%);
  }
  .banner__shapes { position: absolute; inset: 0; }

  .brand {
    position: absolute;
    left: 94px;
    top: 92px;
    display: flex;
    align-items: center;
    gap: 14px;
  }
  .brand__dot {
    width: 34px; height: 34px;
    border-radius: 50%;
    background: var(--pink-hot);
  }
  .brand__name {
    font-weight: 700;
    font-size: 31px;
    color: var(--grey-logo);
    letter-spacing: 0.2px;
  }

  .headline {
    position: absolute;
    left: 94px;
    top: 335px;
  }
  .headline__kicker {
    font-weight: 700;
    font-size: 38px;
    color: var(--white);
    line-height: 1;
  }
  .headline__title {
    margin-top: 38px;
    font-weight: 700;
    font-size: 64px;
    line-height: 96px;
    color: var(--yellow);
    letter-spacing: 1px;
  }

  .features {
    position: absolute;
    left: 95px;
    top: 622px;
    list-style: none;
  }
  .features li {
    font-size: 26px;
    line-height: 42px;
    color: var(--white);
  }

  .cta {
    position: absolute;
    left: 94px;
    top: 945px;
    width: 276px;
    height: 75px;
    border-radius: 38px;
    background: var(--yellow);
    color: var(--purple-mid);
    font-family: "Montserrat", Arial, sans-serif;
    font-weight: 800;
    font-size: 25px;
    display: flex;
    align-items: center;
    justify-content: center;
    letter-spacing: 0.3px;
  }
</style>
</head>
<body>
  <main class="banner">
    <svg class="banner__shapes" width="1200" height="1200" viewBox="0 0 1200 1200">
      <defs>
        <linearGradient id="photoTone" x1="0" y1="1" x2="1" y2="0">
          <stop offset="0" stop-color="#f0407c"/>
          <stop offset="0.6" stop-color="#f47aa3"/>
          <stop offset="1" stop-color="#f9b3c8"/>
        </linearGradient>
      </defs>

      <!-- thin diagonal guide lines -->
      <g stroke="var(--line)" stroke-width="2" fill="none">
        <line x1="0" y1="300" x2="170" y2="0"/>
        <line x1="0" y1="690" x2="390" y2="0"/>
        <line x1="140" y1="1200" x2="820" y2="0"/>
        <line x1="0" y1="1090" x2="560" y2="1090"/>
        <line x1="0" y1="890" x2="380" y2="890"/>
      </g>

      <!-- pink band -->
      <polygon points="290,1200 850,0 1200,0 1200,1200" fill="var(--pink-band)"/>

      <!-- photo area -->
      <polygon role="img" aria-label="Foto: due ragazze sorridenti con borse della spesa gialle e verdi su sfondo rosa"
               points="330,1200 880,0 1200,0 1200,1200" fill="url(#photoTone)"/>

      <!-- accent parallelograms -->
      <polygon points="745,67 806,67 750,212 688,212" fill="var(--pink-hot)"/>
      <polygon points="1070,668 1200,668 1200,700 1090,922 960,922" fill="var(--pink-hot)"/>
      <polygon points="1200,590 1200,668 1160,668" fill="var(--purple-violet)"/>
      <polygon points="1200,740 1200,1200 900,1200 1060,922 1090,922" fill="var(--purple-soft)" opacity="0.85"/>
      <polygon points="238,1062 362,1062 290,1200 166,1200" fill="var(--purple-violet)"/>
      <polygon points="198,1105 262,1105 212,1200 148,1200" fill="var(--pink-hot)"/>
    </svg>

    <div class="brand">
      <span class="brand__dot"></span>
      <span class="brand__name">PagoLume</span>
    </div>

    <header class="headline">
      <p class="headline__kicker">ALL IN ONE!</p>
      <h1 class="headline__title">UNA CARTA<br>PER TUTTI!</h1>
    </header>

    <ul class="features">
      <li>Fai quello che vuoi.</li>
      <li>Nessun limite.</li>
      <li>Nessun controllo</li>
      <li>Privacy garantita</li>
      <li>Usala come vuoi</li>
      <li>Senza essere controllato</li>
    </ul>

    <a class="cta">APPLY NOW</a>
  </main>
</body>
</html>
```